KBT Business Cards

We require business cards for our business. We would like a matte black back to the card, with our logo centred in the middle. The front side of the card is open to design.

Target Market(s)

Clients looking for legal services (professional)

Industry/Entity Type

Legal

Contact Information for Business Card

Doran Kelbrath
Partner
Mobile: 0461 738 524
Email: doran@kbtlaw.co
Website: www.kbtlaw.co
Level 3, 118 Wendmore Street
Sydney NSW 2000

Font styles to use
Other font styles liked:
• Avenir

Colors
f04a50
ffffff
1b1b1b

Requirements
Must have
• Black back with logo included in the centre of the card.
• Our font is Avenir.

```html
<!DOCTYPE html>
<html lang="en">
<head>
<meta charset="UTF-8">
<title>KBT Business Cards</title>
<link rel="stylesheet" href="https://fonts.googleapis.com/css2?family=Roboto:wght@400;500&display=swap">
<style>
  :root {
    --accent: #cf1f45;
    --ink: #2b2b2b;
    --muted: #4a4a4a;
    --paper: #ffffff;
    --card-black: #221f20;
    --backdrop: #e4e4e4;
  }
  * { margin: 0; padding: 0; box-sizing: border-box; }
  html, body {
    width: 1125px;
    height: 1200px;
    overflow: hidden;
  }
  body {
    background: var(--backdrop);
    font-family: "Roboto", sans-serif;
    position: relative;
  }
  .card {
    position: absolute;
    left: 171px;
    width: 826px;
    height: 471px;
  }
  .card--front {
    top: 106px;
    background: var(--paper);
  }
  .card--back {
    top: 639px;
    background: var(--card-black);
  }

  .holder {
    position: absolute;
    right: 41px;
    top: 52px;
    text-align: right;
  }
  .holder__name {
    color: var(--accent);
    font-size: 29px;
    font-weight: 400;
    letter-spacing: 0.3px;
    line-height: 1.1;
  }
  .holder__role {
    color: var(--ink);
    font-size: 20px;
    font-weight: 400;
    letter-spacing: 0.5px;
    line-height: 1.2;
  }

  .contact {
    position: absolute;
    left: 49px;
    top: 352px;
    color: var(--muted);
    font-size: 19px;
    line-height: 1;
  }
  .contact__line { height: 27px; }
  .contact__line--address { margin-top: 5px; }
  .contact__label { color: var(--accent); }

  .brand {
    position: absolute;
    left: 188px;
    top: 168px;
    display: flex;
    align-items: center;
    gap: 40px;
  }
  .brand__square {
    width: 92px;
    height: 92px;
    background: var(--accent);
  }
  .brand__name {
    color: var(--paper);
    font-size: 41px;
    font-weight: 500;
    line-height: 44px;
    letter-spacing: 0.3px;
  }
</style>
</head>
<body>
  <section class="card card--front" aria-label="Business card front">
    <div class="holder">
      <p class="holder__name">DORAN KELBRATH</p>
      <p class="holder__role">PARTNER</p>
    </div>
    <div class="contact">
      <p class="contact__line"><span class="contact__label">M.</span> 0461 738 524</p>
      <p class="contact__line"><span class="contact__label">E.</span> doran@kbtlaw.co <span class="contact__label">W.</span> www.kbtlaw.co</p>
      <p class="contact__line contact__line--address">Level 3, 118 Wendmore Street, Sydney NSW 2000</p>
    </div>
  </section>

  <section class="card card--back" aria-label="Business card back">
    <div class="brand">
      <div class="brand__square"></div>
      <p class="brand__name">KELBRATH<br>BAYNE<br>LEGAL</p>
    </div>
  </section>
</body>
</html>
```